RW Framewell Inc Business cards

We need business cards using our existing logo but slightly modified. Right now the logo says RW Loadbearing Masonry. We want to keep the RW part of the design, but replace the Structural Concrete portion with "FRAMEWELL". Please see the attached file.
Ideally this would be a blank template so we can add Different Names, titles, and phone numbers later.
On the one side we want only the logo and on the other side the detail. I'm attaching an example for you to see.
Please reach out with any other questions. Our address and other details will be given out once we find a design we like.

Target Market(s)

Construction Industry

```html
<!DOCTYPE html>
<html lang="en">
<head>
<meta charset="UTF-8">
<title>RW Framewell Inc — Business Cards</title>
<link href="https://fonts.googleapis.com/css2?family=Archivo+Black&family=Arimo:wght@400&display=swap" rel="stylesheet">
<style>
  :root {
    --backdrop: #2b2b2b;
    --brand-blue: #1c75bd;
    --card-white: #ffffff;
    --text-grey: #7a7a7a;
    --rule-grey: #b5b5b5;
  }
  * { box-sizing: border-box; margin: 0; padding: 0; }
  html, body {
    width: 1200px;
    height: 1040px;
    overflow: hidden;
    background: var(--backdrop);
  }
  .sheet {
    position: relative;
    width: 1200px;
    height: 1040px;
  }
  .card {
    position: absolute;
    left: 220px;
    width: 760px;
    height: 434px;
  }
  .card--front {
    top: 60px;
    background: var(--brand-blue);
    border-radius: 80px 0 80px 0;
    display: flex;
    align-items: center;
    justify-content: center;
  }
  .card--back {
    top: 546px;
    background: var(--card-white);
    border-radius: 0 80px 0 80px;
    display: flex;
    align-items: center;
    padding: 0 0 0 70px;
  }
  .wordmark {
    font-family: "Archivo Black", sans-serif;
    font-weight: 400;
    text-align: center;
    line-height: 1;
  }
  .wordmark__initials {
    display: block;
    font-size: 150px;
    letter-spacing: 4px;
  }
  .wordmark__name {
    display: block;
    font-size: 44px;
    letter-spacing: 3px;
    margin-top: 4px;
  }
  .card--front .wordmark { color: var(--card-white); }
  .card--back .wordmark { color: var(--brand-blue); }
  .card--back .wordmark__initials { font-size: 118px; }
  .card--back .wordmark__name { font-size: 35px; letter-spacing: 2px; }
  .divider {
    width: 1px;
    height: 190px;
    background: var(--rule-grey);
    margin: 0 34px 0 34px;
  }
  .contact {
    font-family: "Arimo", sans-serif;
    color: var(--text-grey);
  }
  .contact__name {
    font-family: "Archivo Black", sans-serif;
    color: var(--brand-blue);
    font-size: 24px;
    letter-spacing: 1px;
    line-height: 1;
  }
  .contact__title {
    font-size: 20px;
    margin: 4px 0 18px;
  }
  .contact__list { list-style: none; }
  .contact__item {
    display: flex;
    align-items: center;
    gap: 10px;
    font-size: 21px;
    margin-bottom: 6px;
  }
  .contact__icon { width: 22px; height: 22px; flex: none; }
  .contact__accent { color: var(--brand-blue); }
</style>
</head>
<body>
<main class="sheet">
  <section class="card card--front" aria-label="Card front">
    <div class="wordmark">
      <span class="wordmark__initials">RW</span>
      <span class="wordmark__name">FRAMEWELL</span>
    </div>
  </section>

  <section class="card card--back" aria-label="Card back">
    <div class="wordmark">
      <span class="wordmark__initials">RW</span>
      <span class="wordmark__name">FRAMEWELL</span>
    </div>
    <div class="divider"></div>
    <div class="contact">
      <p class="contact__name">DANIEL HARPER</p>
      <p class="contact__title">Managing Director</p>
      <ul class="contact__list">
        <li class="contact__item">
          <svg class="contact__icon" viewBox="0 0 24 24" aria-hidden="true"><path d="M6.6 10.8a15.1 15.1 0 0 0 6.6 6.6l2.2-2.2a1 1 0 0 1 1-.25 11.4 11.4 0 0 0 3.6.57 1 1 0 0 1 1 1V20a1 1 0 0 1-1 1A17 17 0 0 1 3 4a1 1 0 0 1 1-1h3.5a1 1 0 0 1 1 1c0 1.25.2 2.45.57 3.57a1 1 0 0 1-.25 1z" fill="var(--brand-blue)"/></svg>
          <span>055-987 654 321</span>
        </li>
        <li class="contact__item">
          <svg class="contact__icon" viewBox="0 0 24 24" aria-hidden="true"><rect x="2" y="5" width="20" height="14" fill="var(--brand-blue)"/><path d="M2 5l10 8 10-8" fill="none" stroke="#fff" stroke-width="1.6"/></svg>
          <span>hello@mailsite.com</span>
        </li>
        <li class="contact__item">
          <svg class="contact__icon" viewBox="0 0 24 24" aria-hidden="true"><g fill="none" stroke="var(--brand-blue)" stroke-width="1.8"><circle cx="12" cy="12" r="9.5"/><ellipse cx="12" cy="12" rx="4.2" ry="9.5"/><path d="M2.5 12h19M4 7h16M4 17h16"/></g></svg>
          <span>www.<span class="contact__accent">framewellsite</span>.com</span>
        </li>
      </ul>
    </div>
  </section>
</main>
</body>
</html>
```